Buch-/eBook-Cover für Traumatherapeutin
Zielgruppe
Ich bin Traumatherapeutin und schreibe ein Buch zum Thema Trauma bearbeiten.
Meine Zielgruppe sucht Heilung, Genesung, Selbstliebe etc.
Aufgabenstellung
Buchcover
Bitte erstell mir ein modernes positives inspirierendes Buchcover mit dem
Titel: 'Morgenlicht NEU entdecken“
Untertitel: „Spüre den Mut der ganz in dir wohnt“
Dr. Mira Kessow
Ich hätte gerne ein modernes Buch, das entweder einen Bezug zum Thema Trauma hat oder aber einfach stylische Schriftzüge. Bin aber auch offen für andere Vorschläge.
Dunkelblau, weiß und türkis oder auch rosa mag ich ganz gerne. Wobei Dunkelblau, weiß und türkis meine Favoriten sind und mit rosa höchstens kleinere Akzente gesetzt werden sollten.
Das Buchcover soll modern sein und direkt ansprechen. Gerne eine originelle Lösung, oder etwas Besonderes, etwas das Tiefe ausdrückt, oder man mehrmals hinsehen muss um etwas zu erkennen oder etwas das mehr Interpretationsspielraum lässt.
Gerne auch viel weiß, zumindest heller und nicht zu dunkel. Stylish, aber nicht überfrachtet.
Schreib mich gerne an, wenn du Fragen hast.
Ich habe mal zwei Beispiel von Typolösungen angehängt, die ich ganz cool fände.
Ich freue mich auf deine Ideen :-)
Ganz liebe Grüße
Mira

```html
<!DOCTYPE html>
<html lang="de">
<head>
<meta charset="utf-8">
<title>Morgenlicht neu entdecken – Buchcover</title>
<link rel="stylesheet" href="https://fonts.googleapis.com/css2?family=Archivo+Black&family=Great+Vibes&family=Jost:wght@500&display=swap">
<style>
  :root {
    --teal: #69b2b8;
    --white: #ffffff;
    --sky-top: #f3ece0;
    --sky-warm: #f7e6c8;
    --sky-rose: #efdcd6;
    --sea: #9fb8cc;
    --sea-deep: #7f9fb8;
    --sand: #f3ece3;
    --grass: #c9a660;
  }
  html, body {
    margin: 0;
    padding: 0;
    width: 848px;
    height: 1200px;
    overflow: hidden;
    background: var(--white);
  }
  .cover {
    position: relative;
    width: 848px;
    height: 1200px;
    overflow: hidden;
    background: var(--teal);
  }
  .cover__photo {
    position: absolute;
    left: 0;
    top: 0;
    width: 848px;
    height: 609px;
    background:
      linear-gradient(90deg, rgba(201,166,96,0.75) 0%, rgba(201,166,96,0.45) 30%, rgba(201,166,96,0) 55%),
      linear-gradient(180deg, var(--sky-top) 0%, var(--sky-warm) 28%, var(--sky-rose) 50%, var(--sea) 55%, var(--sea-deep) 62%, var(--sand) 72%, var(--sand) 100%);
  }
  .cover__title {
    position: absolute;
    left: 0;
    top: 0;
    width: 848px;
    height: 900px;
  }
  .title-main {
    font-family: "Archivo Black", "Arial Black", sans-serif;
    font-size: 104px;
  }
  .title-script {
    font-family: "Great Vibes", cursive;
    fill: var(--white);
  }
  .cover__subtitle {
    position: absolute;
    left: 313px;
    top: 944px;
    width: 440px;
    margin: 0;
    font-family: "Jost", "Futura", sans-serif;
    font-weight: 500;
    font-size: 21px;
    letter-spacing: 0.3px;
    line-height: 37px;
    color: var(--white);
    text-transform: uppercase;
  }
  .cover__subtitle span {
    display: block;
  }
  .cover__subtitle .line-2 {
    text-align: right;
  }
  .cover__author {
    position: absolute;
    left: 311px;
    top: 1056px;
    margin: 0;
    font-family: "Jost", "Futura", sans-serif;
    font-weight: 500;
    font-size: 48px;
    letter-spacing: 0.5px;
    color: var(--white);
    text-transform: uppercase;
  }
</style>
</head>
<body>
<main class="cover">
  <div class="cover__photo" role="img" aria-label="Foto: Dünengras am Strand bei sanftem Sonnenaufgang, ruhiges Meer und heller Himmel"></div>

  <svg class="cover__title" viewBox="0 0 848 900" aria-label="Morgenlicht … neu entdecken!">
    <defs>
      <linearGradient id="title-fill" x1="0" y1="0" x2="0" y2="1">
        <stop offset="0" stop-color="#fbf6ee"/>
        <stop offset="0.55" stop-color="#f2ebe2"/>
        <stop offset="0.75" stop-color="#c9d6df"/>
        <stop offset="1" stop-color="#e9e2d8"/>
      </linearGradient>
      <filter id="title-shadow" x="-5%" y="-20%" width="110%" height="140%">
        <feDropShadow dx="3" dy="4" stdDeviation="2.5" flood-color="#3c5a5e" flood-opacity="0.45"/>
      </filter>
    </defs>

    <text class="title-main" x="24" y="652" textLength="774" lengthAdjust="spacingAndGlyphs"
          fill="url(#title-fill)" filter="url(#title-shadow)">MORGENLICHT</text>

    <text class="title-script" x="206" y="745" font-size="104">… neu</text>
    <text class="title-script" x="318" y="840" font-size="110">entdecken!</text>

    <path d="M303 880 C 380 858, 470 842, 560 838 C 600 836, 598 862, 572 864 C 552 866, 552 848, 574 846"
          fill="none" stroke="var(--white)" stroke-width="2.2" stroke-linecap="round"/>
  </svg>

  <p class="cover__subtitle">
    <span class="line-1">Spüre den Mut,</span>
    <span class="line-2">der ganz in dir wohnt!</span>
  </p>

  <p class="cover__author">Dr. Mira Kessow</p>
</main>
</body>
</html>
```